Northfield Builders Guild Business card

We are looking for a new business card design with photo included.
Our business is a nonprofit construction contractor membership organization. We offer business education, assist with business setup and licensing, provide safety training, and provide a member directory.
URL: www.builderslinkguild.org
Color code:
CMYK: 0 cyan, 42 magenta, 100 yellow, 0 black for Print.
Hexidecimal: #FF9900
RGB: R 255; G 153; B 0

```html
<!DOCTYPE html>
<html lang="en">
<head>
<meta charset="utf-8">
<title>Northfield Builders Guild – Business Card</title>
<link href="https://fonts.googleapis.com/css2?family=Montserrat:wght@600;800&family=Arimo:wght@400&display=swap" rel="stylesheet">
<style>
  :root{
    --orange:#ff9900;
    --orange-pattern:#f59a1f;
    --ink:#1f1f1f;
    --paper:#f4f4f4;
    --paper-pattern:#ececec;
    --stage:#2a2a2a;
  }
  *{box-sizing:border-box;margin:0;padding:0}
  html,body{width:1200px;height:1015px;overflow:hidden}
  body{background:var(--stage);display:flex;flex-direction:column;align-items:center;justify-content:center;gap:56px}
  .card{position:relative;width:700px;height:400px;overflow:hidden;box-shadow:0 12px 30px rgba(0,0,0,.45)}
  .card-pattern{position:absolute;inset:0}
  .card--back{background:var(--orange)}
  .card--back .card-pattern{background:linear-gradient(135deg,var(--orange) 0%,var(--orange-pattern) 50%,var(--orange) 100%)}
  .card--front{background:var(--paper)}
  .card--front .card-pattern{background:linear-gradient(135deg,var(--paper) 0%,var(--paper-pattern) 50%,var(--paper) 100%)}
  .card-content{position:relative;height:100%}

  .brand-name{font-family:"Montserrat",sans-serif;font-weight:800;color:var(--ink);letter-spacing:-.5px;line-height:1}

  /* back */
  .card--back .brand-name{position:absolute;left:80px;top:110px;font-size:38px}
  .back-url{position:absolute;left:82px;top:176px;font-family:"Montserrat",sans-serif;font-weight:600;font-size:20px;letter-spacing:2px;color:var(--ink)}
  .services{position:absolute;left:82px;top:240px;list-style:none;display:grid;grid-template-columns:auto auto;gap:14px 34px;font-family:"Montserrat",sans-serif;font-weight:600;font-size:14px;letter-spacing:.6px;color:var(--ink);text-transform:uppercase}
  .services li{display:flex;align-items:center;gap:8px}
  .bullet{width:11px;height:11px;border-radius:50%;background:var(--ink);flex:none}

  /* front */
  .card--front .brand-name{position:absolute;right:46px;top:48px;font-size:34px;text-align:right;width:420px;line-height:1.05}
  .person{position:absolute;left:60px;top:190px;font-family:"Montserrat",sans-serif}
  .person-name{font-weight:800;font-size:30px;color:var(--orange);text-transform:uppercase;line-height:1}
  .person-title{font-weight:800;font-size:16px;color:var(--ink);text-transform:uppercase;letter-spacing:.5px;margin-top:6px}
  .contacts{position:absolute;left:60px;top:280px;list-style:none;font-family:"Arimo",sans-serif;font-size:17px;color:var(--ink)}
  .contacts li{display:flex;align-items:center;gap:9px;height:25px}
  .contact-icon{width:19px;height:19px;flex:none}
  .address{position:absolute;left:400px;top:220px;font-family:"Arimo",sans-serif;font-size:18px;line-height:1.3;color:var(--ink)}
  .front-url{position:absolute;left:400px;top:310px;font-family:"Arimo",sans-serif;font-size:17px;color:var(--orange)}
</style>
</head>
<body>

<section class="card card--back">
  <div class="card-pattern" role="img" aria-label="Faint repeated brand wordmark pattern across the orange background"></div>
  <div class="card-content">
    <p class="brand-name">NORTHFIELD BUILDERS GUILD</p>
    <p class="back-url">www.builderslinkguild.org</p>
    <ul class="services">
      <li><span class="bullet"></span>Business education</li>
      <li><span class="bullet"></span>Assist with business setup and licensing</li>
      <li><span class="bullet"></span>Provide safety training</li>
      <li><span class="bullet"></span>Provide a member directory</li>
    </ul>
  </div>
</section>

<section class="card card--front">
  <div class="card-pattern" role="img" aria-label="Faint repeated brand wordmark pattern across the white background"></div>
  <div class="card-content">
    <p class="brand-name">NORTHFIELD BUILDERS GUILD</p>
    <div class="person">
      <p class="person-name">Daniel Harper</p>
      <p class="person-title">Managing Director</p>
    </div>
    <ul class="contacts">
      <li>
        <svg class="contact-icon" viewBox="0 0 20 20"><circle cx="10" cy="10" r="10" fill="var(--orange)"/><path d="M6.5 5.5l2 0 1 2.5-1.3 1c.6 1.3 1.5 2.2 2.8 2.8l1-1.3 2.5 1v2c0 .6-.5 1-1 1C9 14.3 5.7 11 5.5 6.5c0-.6.4-1 1-1z" fill="#fff"/></svg>
        (555) 010-4292
      </li>
      <li>
        <svg class="contact-icon" viewBox="0 0 20 20"><circle cx="10" cy="10" r="10" fill="var(--orange)"/><rect x="6.5" y="4.5" width="7" height="11" rx="1.2" fill="none" stroke="#fff" stroke-width="1.5"/><circle cx="10" cy="13.3" r=".8" fill="#fff"/></svg>
        800-555-0125
      </li>
      <li>
        <svg class="contact-icon" viewBox="0 0 20 20"><circle cx="10" cy="10" r="10" fill="var(--orange)"/><rect x="7" y="4.5" width="6" height="3.5" fill="#fff"/><rect x="4.5" y="8" width="11" height="5" rx="1" fill="#fff"/><rect x="7" y="11.5" width="6" height="4" fill="#fff" stroke="var(--orange)" stroke-width=".8"/></svg>
        555.010.0880
      </li>
      <li>
        <svg class="contact-icon" viewBox="0 0 20 20"><circle cx="10" cy="10" r="10" fill="var(--orange)"/><rect x="4.5" y="6.5" width="11" height="7.5" fill="#fff"/><path d="M4.5 6.5l5.5 4.3 5.5-4.3" fill="none" stroke="var(--orange)" stroke-width="1"/></svg>
        support@nbguild.org
      </li>
    </ul>
    <p class="address">4200 Alder Ridge Rd<br>Suite #100, Riverton<br>OR 97000</p>
    <p class="front-url">www.builderslinkguild.org</p>
  </div>
</section>

</body>
</html>
```